Insurance Agency website design for Brellow Cover Insurance, LP

Build a website for Brellow Cover Insurance, LP which sells Homeowners, Auto, Renters, Condo, Flood, Disability, Life, Umbrella, and health insurance. We need the coolest insurance agency website out there to get quotes, contact us, or get additional information. Please list the following insurance companies we work with: Varnix, Ostle, Meridale Mutual, Quillor, Dunmarrow, KGZ, and Pellwick.

Make a design similar to https://www.fernagentry.com/

Selling personal insurance policies

```html
<!DOCTYPE html>
<html lang="en">
<head>
<meta charset="utf-8">
<title>Brellow Cover Insurance, LP</title>
<link href="https://fonts.googleapis.com/css2?family=Montserrat:wght@500;600;700;800&family=Open+Sans:wght@400;600&display=swap" rel="stylesheet">
<style>
:root{
  --navy:#0b3a86;
  --blue:#1456b8;
  --deep:#082c68;
  --green:#7cc242;
  --green-dark:#5fa52c;
  --ink:#1d2a44;
  --muted:#5d6878;
  --line:#dfe5ee;
  --white:#ffffff;
  --soft:#f4f7fb;
}
*{box-sizing:border-box;margin:0;padding:0}
html,body{width:1200px;height:4424px;overflow:hidden}
body{font-family:"Open Sans",Arial,sans-serif;color:var(--ink);background:var(--white);position:relative}
h1,h2,h3,h4,.btn,.brand,.nav a{font-family:"Montserrat",Arial,sans-serif}
.btn{display:inline-block;background:var(--green);color:var(--white);font-weight:600;font-size:15px;padding:14px 30px;border-radius:4px;text-decoration:none}
.btn-navy{background:var(--navy)}
.eyebrow{font-family:"Montserrat",Arial,sans-serif;font-size:13px;font-weight:600;letter-spacing:2px;color:var(--green);text-transform:uppercase;text-align:center}
.section-title{font-size:36px;font-weight:700;color:var(--navy);text-align:center;margin-top:8px}

/* header */
.site-header{position:absolute;top:0;left:0;width:1200px;height:88px;background:var(--white);z-index:3}
.topbar{position:absolute;top:0;right:0;width:620px;height:30px;background:var(--green);clip-path:polygon(24px 0,100% 0,100% 100%,0 100%);display:flex;justify-content:flex-end;align-items:center;gap:34px;padding-right:40px;color:var(--white);font-size:13px}
.topbar span{display:flex;align-items:center;gap:8px}
.brand{position:absolute;left:40px;top:22px;display:flex;align-items:center;gap:10px;font-weight:700;font-size:18px;color:var(--navy);line-height:1.1}
.brand-mark{width:34px;height:34px;background:var(--green);border-radius:4px}
.nav{position:absolute;left:305px;top:46px;display:flex;gap:36px}
.nav a{font-size:14px;font-weight:600;color:var(--ink);text-decoration:none}
.header-cta{position:absolute;right:136px;top:38px;padding:11px 26px;font-size:14px}

/* hero */
.hero{position:absolute;top:88px;left:0;width:1200px;height:732px;overflow:hidden}
.hero-photo{position:absolute;inset:0;background:linear-gradient(90deg,#0a3585 0%,#1b52b0 45%,#8aa6cf 75%,#c7cfd8 100%)}
.hero-copy{position:absolute;left:140px;top:180px;width:620px;color:var(--white)}
.hero-copy h1{font-size:44px;line-height:1.2;font-weight:800}
.hero-copy h1 .light{font-weight:600}
.hero-copy p{font-size:15px;line-height:1.6;margin-top:22px;opacity:.92;width:520px}
.hero-copy .btn{margin-top:34px}
.hero-wave{position:absolute;left:0;bottom:0;width:1200px;height:150px}
.scroll-cue{position:absolute;left:578px;top:800px;width:44px;height:64px;border-radius:22px;background:var(--white);box-shadow:0 4px 14px rgba(11,58,134,.18);z-index:4;display:flex;justify-content:center;padding-top:14px}
.scroll-cue i{display:block;width:14px;height:24px;border:2px solid var(--navy);border-radius:8px}

/* about */
.about{position:absolute;top:960px;left:0;width:1200px;height:380px}
.about-photo{position:absolute;left:152px;top:0;width:268px;height:340px;background:linear-gradient(160deg,#7a8792,#3d4d5f)}
.about-accent{position:absolute;left:130px;top:230px;width:60px;height:130px;background:var(--navy)}
.about-copy{position:absolute;left:480px;top:14px;width:560px}
.about-copy .eyebrow{text-align:left}
.about-copy h2{font-size:30px;font-weight:700;color:var(--navy);margin-top:6px}
.about-copy p{font-size:13px;line-height:1.7;color:var(--muted);margin-top:14px}
.about-copy .btn{margin-top:24px}

/* services */
.services{position:absolute;top:1380px;left:0;width:1200px;height:800px;background:linear-gradient(180deg,#0e3f92,#0a3178)}
.services .eyebrow{margin-top:64px}
.services .section-title{color:var(--white);margin-top:6px}
.card-grid{position:absolute;left:72px;top:170px;width:1056px;display:flex;flex-wrap:wrap;justify-content:center;gap:14px 12px}
.card{width:201px;background:var(--white);border-radius:6px;height:240px;padding:24px 16px;text-align:center}
.card svg{width:44px;height:44px}
.card h3{font-size:16px;font-weight:700;color:var(--navy);margin-top:12px}
.card p{font-size:12.5px;line-height:1.6;color:var(--muted);margin-top:8px}
.services .btn{position:absolute;left:532px;top:716px}

/* partners */
.partners{position:absolute;top:2260px;left:0;width:1200px}
.partner-row{display:flex;justify-content:space-between;align-items:center;width:1060px;margin:54px auto 0}
.partner{font-family:"Montserrat",Arial,sans-serif;font-size:17px;font-weight:700;color:var(--deep);letter-spacing:1px}

/* testimonials */
.testimonials{position:absolute;top:2490px;left:0;width:1200px}
.quote-row{position:absolute;left:140px;top:130px;width:920px;display:flex;gap:40px}
.quote{flex:1;background:var(--white);box-shadow:0 6px 22px rgba(11,58,134,.12);border-radius:6px;height:228px;padding:32px 36px;position:relative}
.quote .mark{font-family:"Montserrat",Arial,sans-serif;font-size:64px;color:var(--line);position:absolute;left:24px;top:-8px;font-weight:800}
.quote p{font-size:13px;line-height:1.7;color:var(--muted);text-align:center;margin-top:10px}
.quote .who{display:flex;align-items:center;justify-content:center;gap:14px;margin-top:22px}
.quote .avatar{width:44px;height:44px;border-radius:50%;background:linear-gradient(135deg,#b79a84,#6d5a50)}
.quote h4{font-size:15px;color:var(--ink)}
.stars{color:#f3b320;font-size:14px;letter-spacing:2px}
.arrow{position:absolute;top:226px;width:40px;height:40px;border-radius:50%;background:var(--white);box-shadow:0 3px 10px rgba(0,0,0,.12);display:flex;align-items:center;justify-content:center}
.dots{position:absolute;left:572px;top:414px;display:flex;gap:8px}
.dots i{width:10px;height:10px;border-radius:50%;background:#c8d2e2}
.dots i.on{background:var(--navy)}

/* quote band */
.quote-band{position:absolute;top:3000px;left:0;width:1200px;height:440px;background:linear-gradient(90deg,#5d9a2a,#8fc25a 60%,#6ea23a);color:var(--white);text-align:center;padding-top:80px}
.quote-band h2{font-size:32px;font-weight:700}
.quote-band p{font-size:14px;line-height:1.6;margin:12px auto 0;width:620px}
.quote-band .btn{margin-top:26px}

/* contact form */
.contact{position:absolute;top:3280px;left:180px;width:840px;height:660px;background:var(--white);border-radius:8px;box-shadow:0 10px 30px rgba(11,58,134,.15);z-index:2;padding:70px 80px 0}
.contact .section-title{font-size:32px}
.form-grid{display:grid;grid-template-columns:1fr 1fr;gap:24px 34px;margin-top:44px}
.field{border-bottom:1px solid var(--line);padding:10px 0;font-size:13px;color:var(--muted)}
.field.wide{grid-column:1/3;height:96px}
.contact .btn{display:block;width:144px;margin:48px auto 0;text-align:center;padding:13px 0}

/* footer */
.site-footer{position:absolute;top:3980px;left:0;width:1200px;height:444px;background:linear-gradient(180deg,#0d3f93,#082f74);color:var(--white)}
.footer-brand{position:absolute;left:140px;top:52px;display:flex;align-items:center;gap:10px;font-family:"Montserrat",Arial,sans-serif;font-weight:700;font-size:17px;width:200px;line-height:1.1}
.footer-brand .brand-mark{width:30px;height:30px}
.footer-blurb{position:absolute;left:340px;top:54px;width:420px;font-size:12.5px;line-height:1.6;opacity:.9}
.socials{position:absolute;right:140px;top:60px;display:flex;gap:12px}
.socials i{width:30px;height:30px;border-radius:50%;background:var(--white)}
.footer-divider{position:absolute;left:140px;top:130px;width:920px;height:1px;background:rgba(255,255,255,.2)}
.contact-info h3{position:absolute;top:160px;width:1200px;text-align:center;font-size:18px;font-weight:700}
.info-cols{position:absolute;top:206px;left:140px;width:920px;display:flex;justify-content:space-between;text-align:center}
.info-cols div{width:260px}
.info-cols svg{width:24px;height:24px}
.info-cols h4{font-size:15px;margin-top:8px}
.info-cols p{font-size:13px;margin-top:6px;opacity:.9;line-height:1.5}
.legal{position:absolute;top:396px;left:140px;width:920px;display:flex;justify-content:space-between;font-size:12.5px;opacity:.9}
.legal span+span{margin-left:24px}
</style>
</head>
<body>

<header class="site-header">
  <div class="topbar">
    <span><svg width="13" height="13" viewBox="0 0 24 24" fill="#fff"><path d="M6.6 10.8a15 15 0 0 0 6.6 6.6l2.2-2.2c.3-.3.7-.4 1-.2 1.1.4 2.3.6 3.6.6.6 0 1 .4 1 1V20c0 .6-.4 1-1 1A17 17 0 0 1 3 4c0-.6.4-1 1-1h3.5c.6 0 1 .4 1 1 0 1.3.2 2.5.6 3.6.1.3 0 .7-.2 1z"/></svg>Phone: (555) 014-2290</span>
    <span><svg width="14" height="12" viewBox="0 0 24 20" fill="#fff"><path d="M2 0h20a2 2 0 0 1 2 2v16a2 2 0 0 1-2 2H2a2 2 0 0 1-2-2V2a2 2 0 0 1 2-2zm10 9L2 3v2l10 6 10-6V3z"/></svg>E-mail: info@brellowcover.com</span>
  </div>
  <div class="brand"><span class="brand-mark"></span><span>Brellow Cover<br>Insurance</span></div>
  <nav class="nav"><a>HOME</a><a>ABOUT US</a><a>INSURANCE ▾</a><a>MARKET PARTNERS</a></nav>
  <a class="btn btn-navy header-cta">Get a Quote</a>
</header>

<section class="hero">
  <div class="hero-photo" role="img" aria-label="Photo of a smiling family on the floor of their new home holding a cardboard roof over their heads"></div>
  <div class="hero-copy">
    <h1>Protect What Matters<br><span class="light">Most with Trusted</span><br>Insurance</h1>
    <p>At Brellow Cover Insurance, we understand how important it is to protect the things that matter most to you – your home, family, and future.</p>
    <a class="btn">Get Your Quote Now</a>
  </div>
  <svg class="hero-wave" viewBox="0 0 1200 150" preserveAspectRatio="none">
    <path d="M0 70 Q600 170 1200 40 L1200 150 L0 150 Z" fill="#7cc242"/>
    <path d="M0 96 Q600 190 1200 70 L1200 150 L0 150 Z" fill="#ffffff"/>
  </svg>
</section>
<div class="scroll-cue"><i></i></div>

<section class="about">
  <div class="about-accent"></div>
  <div class="about-photo" role="img" aria-label="Photo of an agent handing house keys to a couple outside their home"></div>
  <div class="about-copy">
    <div class="eyebrow">Who We Are</div>
    <h2>About Brellow Cover Insurance</h2>
    <p>At Brellow Cover Insurance, we're dedicated to providing you with reliable, comprehensive insurance solutions tailored to your needs. Our mission is simple: to offer you peace of mind with the protection you deserve. We specialize in home, auto, health, and life insurance, and our experienced team is committed to helping you find the right coverage for every stage of life.</p>
    <p>Founded with a focus on customer satisfaction, Brellow Cover Insurance has grown to become a trusted partner in securing what matters most. With years of industry experience, we prioritize clear communication and personalized service. Our clients' needs are at the heart of everything we do, and we work tirelessly to ensure they have the best protection available.</p>
    <a class="btn">Learn More</a>
  </div>
</section>

<section class="services">
  <div class="eyebrow">Our Insurances</div>
  <h2 class="section-title">Our Various Insurance Solutions</h2>
  <div class="card-grid">
    <div class="card"><svg viewBox="0 0 44 44"><rect width="44" height="44" rx="8" fill="#1456b8"/><path d="M10 23 22 12l12 11h-4v10h-6v-7h-4v7h-6V23z" fill="#fff"/></svg><h3>Homeowners</h3><p>Protect your home and belongings from damage, theft, or disaster with comprehensive homeowners coverage.</p></div>
    <div class="card"><svg viewBox="0 0 44 44"><rect width="44" height="44" rx="8" fill="#1456b8"/><path d="M11 27v-5l3-7h16l3 7v5h-3v3h-4v-3H18v3h-4v-3zm4-6h14l-2-4H17z" fill="#fff"/></svg><h3>Auto Insurance</h3><p>Safeguard your vehicle against accidents, theft, and damage, ensuring you're covered on the road.</p></div>
    <div class="card"><svg viewBox="0 0 44 44"><rect width="44" height="44" rx="8" fill="#1456b8"/><path d="M12 32V14h20v18h-7v-6h-6v6zm4-14v3h3v-3zm9 0v3h3v-3z" fill="#fff"/></svg><h3>Renters Insurance</h3><p>Protect personal belongings in a rented space, covering damage, theft, or loss due to disasters.</p></div>
    <div class="card"><svg viewBox="0 0 44 44"><rect width="44" height="44" rx="8" fill="#1456b8"/><path d="M13 33V11h12v6h6v16h-6v-5h-6v5zm3-18v3h3v-3zm0 6v3h3v-3z" fill="#fff"/></svg><h3>Condo Insurance</h3><p>Cover your condo unit and personal property, filling the gaps not covered by the building's insurance.</p></div>
    <div class="card"><svg viewBox="0 0 44 44"><rect width="44" height="44" rx="8" fill="#1456b8"/><path d="M22 10c5 7 8 11 8 15a8 8 0 0 1-16 0c0-4 3-8 8-15z" fill="#fff"/></svg><h3>Flood Insurance</h3><p>Provide financial protection against water damage caused by floods, which are often excluded from standard coverage.</p></div>
    <div class="card"><svg viewBox="0 0 44 44"><rect width="44" height="44" rx="8" fill="#1456b8"/><circle cx="22" cy="12" r="3" fill="#fff"/><path d="M20 17h4v7h5v3h-8zM17 22a8 8 0 1 0 11 9" stroke="#fff" stroke-width="2.5" fill="none"/></svg><h3>Disability Insurance</h3><p>Receive income replacement if you're unable to work due to illness or injury, ensuring financial security.</p></div>
    <div class="card"><svg viewBox="0 0 44 44"><rect width="44" height="44" rx="8" fill="#1456b8"/><path d="M22 32s-10-6-10-13a5 5 0 0 1 10-2 5 5 0 0 1 10 2c0 7-10 13-10 13z" fill="#fff"/></svg><h3>Life Insurance</h3><p>Protect your loved ones financially after your passing, covering funeral expenses and ongoing living costs.</p></div>
    <div class="card"><svg viewBox="0 0 44 44"><rect width="44" height="44" rx="8" fill="#1456b8"/><path d="M11 23a11 11 0 0 1 22 0z" fill="#fff"/><path d="M22 23v8a2 2 0 0 1-4 0" stroke="#fff" stroke-width="2.5" fill="none"/></svg><h3>Umbrella Insurance</h3><p>Add extra liability protection beyond your home and auto limits, guarding your savings from large claims.</p></div>
    <div class="card"><svg viewBox="0 0 44 44"><rect width="44" height="44" rx="8" fill="#1456b8"/><path d="M22 10l10 4v7c0 7-5 11-10 13-5-2-10-6-10-13v-7z" fill="#fff"/><path d="M20 17h4v3h3v4h-3v3h-4v-3h-3v-4h3z" fill="#1456b8"/></svg><h3>Health Insurance</h3><p>Cover medical expenses from check-ups to emergencies, ensuring you get the care you need without financial strain.</p></div>
  </div>
  <a class="btn">Explore All</a>
</section>

<section class="partners">
  <div class="eyebrow">Our Partners</div>
  <h2 class="section-title">Trusted Partners for Your Protection</h2>
  <div class="partner-row">
    <span class="partner">VARNIX</span><span class="partner">Ostle</span><span class="partner">MERIDALE MUTUAL</span><span class="partner">Quillor</span><span class="partner">DUNMARROW</span><span class="partner">KGZ</span><span class="partner">PELLWICK</span>
  </div>
</section>

<section class="testimonials">
  <div class="eyebrow">Clients Testimonials</div>
  <h2 class="section-title">Proven Success Stories</h2>
  <div class="arrow" style="left:94px"><svg width="12" height="12" viewBox="0 0 12 12"><path d="M8 1 3 6l5 5" stroke="#0b3a86" stroke-width="2" fill="none"/></svg></div>
  <div class="arrow" style="right:94px"><svg width="12" height="12" viewBox="0 0 12 12"><path d="M4 1l5 5-5 5" stroke="#0b3a86" stroke-width="2" fill="none"/></svg></div>
  <div class="quote-row">
    <div class="quote"><span class="mark">“</span><p>The team walked us through every option and found a home and auto bundle that saved us money. When a storm hit last spring, our claim was handled quickly and with real care from start to finish.</p><div class="who"><span class="avatar"></span><div><h4>Rhea Calloway</h4><div class="stars">★★★★★</div></div></div></div>
    <div class="quote"><span class="mark">“</span><p>I switched my renters and life policies here and could not be happier. They answered every question clearly, checked in after signing, and made the whole process feel simple, honest and friendly.</p><div class="who"><span class="avatar"></span><div><h4>Toby Wrennick</h4><div class="stars">★★★★★</div></div></div></div>
  </div>
  <div class="dots"><i></i><i></i><i class="on"></i><i></i></div>
</section>

<section class="quote-band" role="img" aria-label="Green-tinted photo of a family outdoors behind the quote call to action">
  <h2>Secure a Future with Customized Quote Today!</h2>
  <p>Protect what matters most with trusted insurance solutions. Get a personalized quote today and secure peace of mind.</p>
  <a class="btn btn-navy">Get a Quote</a>
</section>

<section class="contact">
  <div class="eyebrow">Contact Us</div>
  <h2 class="section-title">Get in Touch with Us</h2>
  <div class="form-grid">
    <div class="field">Your First Name *</div>
    <div class="field">Your Last Name *</div>
    <div class="field">Enter Your Email Address *</div>
    <div class="field">Your Phone Number *</div>
    <div class="field wide">Your Message</div>
  </div>
  <a class="btn">Submit Now</a>
</section>

<footer class="site-footer">
  <div class="footer-brand"><span class="brand-mark"></span><span>Brellow Cover<br>Insurance</span></div>
  <p class="footer-blurb">At Brellow Cover Insurance, we're dedicated to providing you with reliable, comprehensive insurance solutions tailored to your needs.</p>
  <div class="socials"><i></i><i></i><i></i></div>
  <div class="footer-divider"></div>
  <div class="contact-info"><h3>Contact Information</h3></div>
  <div class="info-cols">
    <div><svg viewBox="0 0 24 24" fill="#7cc242"><path d="M6.6 10.8a15 15 0 0 0 6.6 6.6l2.2-2.2c.3-.3.7-.4 1-.2 1.1.4 2.3.6 3.6.6.6 0 1 .4 1 1V20c0 .6-.4 1-1 1A17 17 0 0 1 3 4c0-.6.4-1 1-1h3.5c.6 0 1 .4 1 1 0 1.3.2 2.5.6 3.6.1.3 0 .7-.2 1z"/></svg><h4>Call Us</h4><p>(555) 014-2290</p></div>
    <div><svg viewBox="0 0 24 24" fill="#7cc242"><path d="M12 2a7 7 0 0 1 7 7c0 5-7 13-7 13S5 14 5 9a7 7 0 0 1 7-7zm0 4a3 3 0 1 0 0 6 3 3 0 0 0 0-6z"/></svg><h4>Find Us</h4><p>101 Larkfield Ave, Suite 3,<br>Denvale</p></div>
    <div><svg viewBox="0 0 24 20" fill="#7cc242"><path d="M2 0h20a2 2 0 0 1 2 2v16a2 2 0 0 1-2 2H2a2 2 0 0 1-2-2V2a2 2 0 0 1 2-2zm10 9L2 3v2l10 6 10-6V3z"/></svg><h4>Email Address</h4><p>info@brellowcover.com</p></div>
  </div>
  <div class="legal"><span>Copyright © 2025 Brellow Cover Insurance, LP - All Rights Reserved.</span><div><span>Terms of use</span><span>Privacy Policy</span></div></div>
</footer>

</body>
</html>
```